Parcelwise HQ letterhead and envelope

Design a formal (8.5x11) letterhead and envelope for sales outreach and legal matters. Using design input from https://www.parcelwisehq.example/ and the attached documents.

Industry/Entity Type

Software Service

Requirements
Must have
• These 4 hex colors are our official colors:
• #355c98 [blue]
• #1eb1a2 [teal]
• #fdba12 [gold]
• #f1653b [orange]
• So no other colors besides these should be used.

```html
<!DOCTYPE html>
<html lang="en">
<head>
<meta charset="utf-8">
<title>Parcelwise HQ Letterhead</title>
<link href="https://fonts.googleapis.com/css2?family=Open+Sans:wght@400;600;700&display=swap" rel="stylesheet">
<style>
  :root {
    --brand-blue: #355c98;
    --brand-teal: #1eb1a2;
    --ink: #2b2b2b;
    --paper: #ffffff;
    --backdrop: #ececec;
    --signature-tone: #d7dde8;
  }
  * { box-sizing: border-box; margin: 0; padding: 0; }
  html, body {
    width: 1200px; height: 784px; overflow: hidden;
    background: var(--backdrop);
    font-family: "Open Sans", Arial, sans-serif;
  }
  .letterhead {
    position: absolute; left: 320px; top: 30px;
    width: 560px; height: 724px;
    background: var(--paper);
    box-shadow: 0 6px 24px rgba(0,0,0,0.12);
    overflow: hidden;
  }
  .brand {
    position: absolute; left: 44px; top: 44px;
    display: flex; align-items: center; gap: 8px;
  }
  .brand-dot {
    width: 18px; height: 18px; border-radius: 50%;
    border: 2px solid var(--brand-blue);
  }
  .brand-name {
    color: var(--brand-blue); font-size: 20px; font-weight: 400;
    letter-spacing: 0.2px;
  }
  .letter-body {
    position: absolute; left: 72px; top: 118px; width: 372px;
    color: var(--ink); font-size: 9px; line-height: 1.55;
  }
  .salutation { font-weight: 700; font-size: 11px; margin-bottom: 12px; }
  .letter-body p { margin-bottom: 11px; }
  .signature {
    display: block; width: 100px; height: 32px; margin-top: 4px;
    background: var(--signature-tone); border-radius: 4px;
  }
  .footer-wave { position: absolute; left: 0; top: 0; width: 560px; height: 724px; }
  .footer-contact {
    position: absolute; right: 16px; bottom: 12px;
    color: var(--paper); font-size: 8px; line-height: 1.6; text-align: right;
    white-space: nowrap;
  }
  .footer-contact .company { font-weight: 700; font-size: 10px; }
  .contact-row { display: flex; justify-content: flex-end; gap: 10px; }
  .contact-item { display: inline-flex; align-items: center; gap: 3px; white-space: nowrap; }
  .contact-item svg { width: 9px; height: 9px; flex: none; }
</style>
</head>
<body>
  <main class="letterhead">
    <svg class="footer-wave" viewBox="0 0 560 724" aria-hidden="true">
      <path d="M0,690 C200,685 360,645 450,575 C510,525 545,405 560,305" fill="none" stroke="var(--brand-teal)" stroke-width="6"/>
      <path d="M0,702 C200,697 360,657 450,587 C510,537 545,417 560,317 L560,724 L0,724 Z" fill="var(--brand-blue)"/>
    </svg>

    <header class="brand">
      <span class="brand-dot"></span>
      <span class="brand-name">Parcelwise HQ</span>
    </header>

    <section class="letter-body">
      <p class="salutation">Dear Mr. Alder,</p>
      <p>Lorem Ipsum is simply dummy text of the printing and typesetting industry. Lorem Ipsum has been the industry's standard dummy text ever since the 1500s, when an unknown printer took a galley of type and scrambled it to make a type specimen book. It has survived not only five centuries, but also the leap into electronic typesetting, remaining essentially unchanged.</p>
      <p>The standard chunk of Lorem Ipsum used since the 1500s is reproduced below for those interested. Sections 1.10.32 and 1.10.33 from "de Finibus Bonorum et Malorum" by Cicero are also reproduced in their exact original form, accompanied by English versions from the 1914 translation by H. Rackham.</p>
      <p>Lorem Ipsum is simply dummy text of the printing and typesetting industry. Lorem Ipsum has been the industry's standard dummy text ever since the 1500s, when an unknown printer took a galley of type and scrambled it to make a type specimen book. It has survived not only five centuries, but also the leap into electronic typesetting, remaining essentially unchanged. It was popularised in the</p>
      <p>The standard chunk of Lorem Ipsum used since the 1500s is reproduced below for those interested. Sections 1.10.32 and 1.10.33 from "de Finibus Bonorum et Malorum" by Cicero are also reproduced in their exact original form, accompanied by English versions from the 1914 translation by H. Rackham</p>
      <span class="signature" role="img" aria-label="Handwritten signature of the sender"></span>
    </section>

    <footer class="footer-contact">
      <div class="company">Parcelwise HQ</div>
      <div>42 Harbor Lane Eastfield, OR 97000</div>
      <div class="contact-row">
        <span class="contact-item">
          <svg viewBox="0 0 10 10"><circle cx="5" cy="5" r="5" fill="#fff"/><path d="M3.2 2.6l1 1-.5.7a3 3 0 0 0 2 2l.7-.5 1 1-.6.8c-2 0-4-2-4-4z" fill="var(--brand-blue)"/></svg>
          (555) 014-2290
        </span>
        <span class="contact-item">
          <svg viewBox="0 0 10 10"><circle cx="5" cy="5" r="5" fill="#fff"/><rect x="2.5" y="3.3" width="5" height="3.4" fill="none" stroke="var(--brand-blue)" stroke-width=".8"/><path d="M2.5 3.3L5 5.3 7.5 3.3" fill="none" stroke="var(--brand-blue)" stroke-width=".8"/></svg>
          mreyes@parcelwisehq.example
        </span>
        <span class="contact-item">
          <svg viewBox="0 0 10 10"><circle cx="5" cy="5" r="5" fill="#fff"/><circle cx="5" cy="5" r="2.6" fill="none" stroke="var(--brand-blue)" stroke-width=".8"/><path d="M2.4 5h5.2M5 2.4v5.2" stroke="var(--brand-blue)" stroke-width=".6"/></svg>
          www.parcelwisehq.example
        </span>
      </div>
    </footer>
  </main>
</body>
</html>
```